Business Cards for a law firm

Business cards for our law firm. Use our silhoette logo and OAK PARTNERS - check our website (www.oakpartners.example)

Contact Information for Business Card

our silhouette logo, OAK PARTNERS, 800-555-0147, Dorian Pemberton, dorian@oakpartners.example

Requirements
Must have
• our silhouette logo, OAK PARTNERS, 800-555-0147, Dorian Pemberton, dorian@oakpartners.example

```html
<!DOCTYPE html>
<html lang="en">
<head>
<meta charset="utf-8">
<title>Oak Partners Business Cards</title>
<link rel="stylesheet" href="https://fonts.googleapis.com/css2?family=Montserrat:wght@500;600&family=Open+Sans:wght@400;700&display=swap">
<style>
  :root {
    --navy: #1f2f72;
    --navy-deep: #17245c;
    --navy-soft: #2c3f8f;
    --white: #ffffff;
    --ink: #2a2a2a;
    --backdrop: #2b2c2e;
  }
  * { margin: 0; padding: 0; box-sizing: border-box; }
  html, body { width: 1200px; height: 900px; overflow: hidden; }
  body {
    background: var(--backdrop);
    display: flex;
    flex-direction: column;
    align-items: center;
    justify-content: center;
    gap: 40px;
    font-family: "Open Sans", Arial, sans-serif;
  }
  .card {
    position: relative;
    width: 700px;
    height: 400px;
    overflow: hidden;
    box-shadow: 0 10px 30px rgba(0,0,0,0.45);
  }
  /* Front */
  .card-front { background: var(--white); }
  .front-swoosh { position: absolute; inset: 0; }
  .brand-name {
    position: absolute;
    left: 150px;
    top: 52px;
    font-family: "Montserrat", Arial, sans-serif;
    font-weight: 600;
    font-size: 48px;
    letter-spacing: 5px;
    color: var(--navy);
  }
  .person {
    position: absolute;
    right: 410px;
    top: 150px;
    text-align: right;
  }
  .person-name { font-weight: 700; font-size: 22px; color: var(--navy); }
  .person-title { font-size: 15px; color: var(--ink); margin-top: 2px; }
  .divider {
    position: absolute;
    left: 305px;
    top: 160px;
    width: 1.5px;
    height: 78px;
    background: var(--navy);
  }
  .contacts {
    position: absolute;
    left: 320px;
    top: 160px;
    list-style: none;
    font-size: 15px;
    color: var(--ink);
    line-height: 26px;
  }
  .contacts li { display: flex; align-items: center; gap: 8px; }
  .contacts svg { width: 13px; height: 13px; fill: var(--navy); flex: none; }
  /* Back */
  .card-back { background: var(--navy); }
  .back-pattern {
    position: absolute;
    inset: 0;
    background: linear-gradient(160deg, var(--navy-soft) 0%, var(--navy) 45%, var(--navy-deep) 100%);
  }
  .back-brand {
    position: absolute;
    inset: 0;
    display: flex;
    align-items: center;
    justify-content: center;
    font-family: "Montserrat", Arial, sans-serif;
    font-weight: 500;
    font-size: 34px;
    letter-spacing: 5px;
    color: var(--white);
  }
</style>
</head>
<body>
  <section class="card card-front">
    <svg class="front-swoosh" viewBox="0 0 700 400" width="700" height="400" aria-hidden="true">
      <path d="M0 175 C 90 330, 330 388, 700 400 L0 400 Z" fill="var(--navy)"/>
      <path d="M18 140 C 110 300, 360 372, 580 388" fill="none" stroke="var(--navy)" stroke-width="3"/>
    </svg>
    <div class="brand-name">OAK PARTNERS</div>
    <div class="person">
      <div class="person-name">Dorian Pemberton</div>
      <div class="person-title">Lawyer</div>
    </div>
    <div class="divider"></div>
    <ul class="contacts">
      <li>
        <svg viewBox="0 0 24 24" aria-hidden="true"><path d="M6.6 10.8a15 15 0 0 0 6.6 6.6l2.2-2.2c.3-.3.7-.4 1-.2 1.1.4 2.3.6 3.6.6.6 0 1 .4 1 1V20c0 .6-.4 1-1 1A17 17 0 0 1 3 4c0-.6.4-1 1-1h3.5c.6 0 1 .4 1 1 0 1.3.2 2.5.6 3.6.1.3 0 .7-.2 1z"/></svg>
        800-555-0147
      </li>
      <li>
        <svg viewBox="0 0 24 24" aria-hidden="true"><path d="M2 5h20v14H2z M2 5l10 8 10-8" /></svg>
        dorian@oakpartners.example
      </li>
      <li>
        <svg viewBox="0 0 24 24" aria-hidden="true"><path d="M12 2a10 10 0 1 0 0 20 10 10 0 0 0 0-20zm6.9 9h-3a15 15 0 0 0-1.3-5.6A8 8 0 0 1 18.9 11zM12 4.1c.9 1.3 1.7 3.7 1.9 6.9h-3.8c.2-3.2 1-5.6 1.9-6.9zM9.4 5.4A15 15 0 0 0 8.1 11h-3a8 8 0 0 1 4.3-5.6zM5.1 13h3a15 15 0 0 0 1.3 5.6A8 8 0 0 1 5.1 13zm6.9 6.9c-.9-1.3-1.7-3.7-1.9-6.9h3.8c-.2 3.2-1 5.6-1.9 6.9zm2.6-1.3a15 15 0 0 0 1.3-5.6h3a8 8 0 0 1-4.3 5.6z"/></svg>
        www.oakpartners.example
      </li>
    </ul>
  </section>

  <section class="card card-back">
    <div class="back-pattern" role="img" aria-label="Repeating tone-on-tone pattern of the firm's silhouette emblem"></div>
    <div class="back-brand">OAK PARTNERS</div>
  </section>
</body>
</html>
```